Business Card - high end, modern health care

Hey designers!

We need a double sided business card for the boutique, cutting edge physical therapy rehabilitation centre in Sydney's Northern Beaches.

With the most qualified physios in the area The Harbourview Motion Clinic does what other physiotherapy practices do not, we take our time with our patients giving them longer appointments, better physios and therefor faster results!

We guarantee that the service people receive at THMC will be unparalleled.

Hence we need a business card to reflect our modern, boutique, high end service. The final design needs to reflect that we are in a class of our own yet with the feel of beachside retreat.

Below I have attached our logo in both blue on white and white on blue. The exact colour is;
and the font that we have used in our logo is Tex Gyre Aventador.

I like the idea of the blue as the main colour as it is more eye catching and our signage onto the main road will be in this blue and in the interest of consistency across marketing the blue needs to be a part of the design. However I would appreciate a few designs onto a wooden background as this is a visual theme within the fitout of the practice.

The design needs to be of standard size (91x55mm).

Target Market(s)

We target people who have an end outcome in mind and those who have had poor experiences with other providers and ensure that everyone gets the care that they deserve with a premium service that is tailored to the individuals circumstances. As a premium service, the target market is highly educated, business and tech savvy with the additional target market of elderly people who have self funded their retirement and see value in paying for the best ongoing rehabilitation to maintain independence.

Industry/Entity Type

Physical Therapy

Contact Information for Business Card

Name, designation( Titled Musculoskeletal Physiotherapist... there will also be those in the company that have multiple designations ie 5 or 6 words long), phone number, email, facebook, instagram, address

Font styles to use
Sans Serif

Colors

Designer to choose colors to be used in the design.

Requirements
Must have
• Front - The logo as large as possible, blue or wooden theme, and all of the important details.
• Back - A blank space/lines on which to write appointment times (no "Appointment, date, time" etc.)
Nice to have
• facebook url
• logos for facebook and instagram
• Mini logos for the phone and email?

```html
<!DOCTYPE html>
<html lang="en">
<head>
<meta charset="utf-8">
<title>The Harbourview Motion Clinic – Business Card</title>
<link href="https://fonts.googleapis.com/css2?family=Open+Sans:wght@400;600;700&display=swap" rel="stylesheet">
<style>
  :root {
    --brand-blue: #0f5aa8;
    --ink-dark: #2f2f2f;
    --paper: #ffffff;
    --stage: #000000;
    --text-grey: #3a3a3a;
  }
  * { box-sizing: border-box; margin: 0; padding: 0; }
  html, body {
    width: 1200px; height: 900px; overflow: hidden;
    background: var(--stage);
    font-family: "Open Sans", Arial, sans-serif;
  }
  .canvas { position: relative; width: 1200px; height: 900px; }

  .card {
    position: absolute; width: 620px; height: 376px;
    border-radius: 28px; overflow: hidden;
  }
  .card-front { left: 290px; top: 40px; background: var(--paper); }
  .card-back  { left: 290px; top: 484px; background: var(--brand-blue); }
  .card-shapes { position: absolute; inset: 0; }

  /* Front */
  .brand-block {
    position: absolute; left: 150px; top: 30px; width: 300px;
    display: flex; flex-direction: column; align-items: center; gap: 14px;
  }
  .brand-dot { width: 100px; height: 100px; border-radius: 50%; background: var(--brand-blue); }
  .brand-name {
    color: var(--brand-blue); font-weight: 700; font-size: 15px;
    letter-spacing: 1px; text-transform: uppercase; text-align: center; line-height: 1.25;
  }
  .person {
    position: absolute; right: 30px; top: 184px; text-align: right;
  }
  .person-name { color: var(--brand-blue); font-size: 26px; font-weight: 400; line-height: 1; letter-spacing: 0.5px; }
  .person-title { color: var(--text-grey); font-size: 13px; font-weight: 600; margin-top: 5px; line-height: 18px; }
  .contact-list {
    position: absolute; left: 28px; top: 258px; list-style: none;
    color: var(--text-grey); font-size: 11.5px; font-weight: 600; line-height: 19px;
  }
  .contact-list li { display: flex; align-items: center; gap: 7px; }
  .contact-list svg { width: 12px; height: 12px; flex: none; }
  .web-strip {
    position: absolute; left: 16px; bottom: 6px; display: flex; align-items: center; gap: 6px;
    color: var(--paper); font-size: 11px; font-weight: 600;
  }
  .web-strip svg { width: 12px; height: 12px; }
  .address {
    position: absolute; left: 290px; bottom: 26px; display: flex; align-items: center; gap: 14px;
    color: var(--paper); font-size: 16px; line-height: 1.3;
  }
  .address svg { width: 24px; height: 30px; flex: none; }

  /* Back */
  .back-brand {
    position: absolute; left: 330px; top: 26px; width: 200px;
    display: flex; flex-direction: column; align-items: center; gap: 8px;
  }
  .back-brand .brand-dot { width: 66px; height: 66px; background: var(--paper); }
  .back-brand .brand-name { color: var(--paper); font-size: 11px; }
  .appointment-fields {
    position: absolute; left: 44px; top: 126px; width: 500px; list-style: none;
  }
  .appointment-fields li {
    display: flex; align-items: flex-end; gap: 8px; height: 34px;
    color: rgba(255,255,255,0.75); font-size: 15px;
  }
  .appointment-fields .rule { flex: 1; border-bottom: 1.5px solid rgba(255,255,255,0.9); margin-bottom: 4px; }
  .back-web {
    position: absolute; left: 16px; bottom: 6px; display: flex; align-items: center; gap: 6px;
    color: var(--brand-blue); font-size: 11px; font-weight: 600;
  }
  .back-web svg { width: 12px; height: 12px; }
</style>
</head>
<body>
<main class="canvas">

  <!-- Front side -->
  <section class="card card-front" aria-label="Business card front">
    <svg class="card-shapes" viewBox="0 0 620 376" aria-hidden="true">
      <line x1="0" y1="244" x2="620" y2="244" stroke="var(--brand-blue)" stroke-width="1.5"/>
      <polygon points="0,348 236,348 226,376 0,376" fill="var(--ink-dark)"/>
      <polygon points="262,270 620,270 620,376 222,376" fill="var(--brand-blue)"/>
    </svg>

    <div class="brand-block">
      <span class="brand-dot"></span>
      <p class="brand-name">The Harbourview Motion Clinic</p>
    </div>

    <div class="person">
      <p class="person-name">YOUR NAME</p>
      <p class="person-title">Musculoskeletal Physiotherapist</p>
    </div>

    <ul class="contact-list">
      <li>
        <svg viewBox="0 0 12 12"><path d="M2 1.5 4 1l1 2.5-1.2.9a6 6 0 0 0 3.8 3.8l.9-1.2L11 8l-.5 2A1.5 1.5 0 0 1 9 11 8 8 0 0 1 1 3a1.5 1.5 0 0 1 1-1.5z" fill="var(--brand-blue)"/></svg>
        +00 4821 337 560
      </li>
      <li>
        <svg viewBox="0 0 12 12"><rect x="0.75" y="2.25" width="10.5" height="7.5" fill="none" stroke="var(--brand-blue)" stroke-width="1"/><path d="M1 2.5 6 6.5l5-4" fill="none" stroke="var(--brand-blue)" stroke-width="1"/></svg>
        yourname@mailbox.com
      </li>
      <li>
        <svg viewBox="0 0 12 12"><rect x="1" y="1" width="10" height="10" rx="1.5" fill="none" stroke="var(--brand-blue)" stroke-width="1.2"/></svg>
        yourprofilepage.com
      </li>
      <li>
        <svg viewBox="0 0 12 12"><circle cx="6" cy="6" r="5" fill="none" stroke="var(--brand-blue)" stroke-width="1.2"/></svg>
        yourphotopage.com
      </li>
    </ul>

    <p class="web-strip">
      <svg viewBox="0 0 12 12"><circle cx="6" cy="6" r="5" fill="none" stroke="currentColor"/><ellipse cx="6" cy="6" rx="2.2" ry="5" fill="none" stroke="currentColor" stroke-width="0.8"/><line x1="1" y1="6" x2="11" y2="6" stroke="currentColor" stroke-width="0.8"/></svg>
      www.harbourviewmotion.com
    </p>

    <div class="address">
      <svg viewBox="0 0 24 30"><path d="M12 1.5a9 9 0 0 0-9 9c0 7 9 17.5 9 17.5s9-10.5 9-17.5a9 9 0 0 0-9-9z" fill="none" stroke="currentColor" stroke-width="1.6"/><circle cx="12" cy="10.5" r="3.4" fill="none" stroke="currentColor" stroke-width="1.6"/></svg>
      <p>14 Shoreline Parade,<br>Harbourview 2100</p>
    </div>
  </section>

  <!-- Back side -->
  <section class="card card-back" aria-label="Business card back">
    <svg class="card-shapes" viewBox="0 0 620 376" aria-hidden="true">
      <polygon points="0,348 262,348 252,376 0,376" fill="var(--paper)"/>
      <polygon points="290,338 620,306 620,376 262,376" fill="var(--ink-dark)"/>
    </svg>

    <div class="back-brand">
      <span class="brand-dot"></span>
      <p class="brand-name">The Harbourview Motion Clinic</p>
    </div>

    <ul class="appointment-fields">
      <li>Appointment <span class="rule"></span></li>
      <li>Date <span class="rule"></span></li>
      <li>Time <span class="rule"></span></li>
      <li><span class="rule"></span></li>
      <li><span class="rule"></span></li>
    </ul>

    <p class="back-web">
      <svg viewBox="0 0 12 12"><circle cx="6" cy="6" r="5" fill="none" stroke="currentColor"/><ellipse cx="6" cy="6" rx="2.2" ry="5" fill="none" stroke="currentColor" stroke-width="0.8"/><line x1="1" y1="6" x2="11" y2="6" stroke="currentColor" stroke-width="0.8"/></svg>
      www.harbourviewmotion.com
    </p>
  </section>

</main>
</body>
</html>
```